Stationery and Business Card Design

We need stationary design for our new company lanternfold. Lanternfold is a company that provides city apartment rentals for tourists in Athens We need business cards, letterheads for A4 and A5 and envelopes for A4 A5. The design needs to be modern, friendly and corporate.

Target Market(s)

City Tourists

Industry/Entity Type

Tourism

```html
<!DOCTYPE html>
<html lang="en">
<head>
<meta charset="utf-8">
<title>Lanternfold Business Card</title>
<link rel="stylesheet" href="https://fonts.googleapis.com/css2?family=Raleway:wght@400;500;600&display=swap">
<style>
  :root {
    --backdrop: #a9a7a8;
    --plum: #84205a;
    --paper: #f7f7f7;
    --charcoal: #3f3b3c;
    --ink: #4a4a4a;
    --rule: #e2e2e2;
  }
  * { margin: 0; padding: 0; box-sizing: border-box; }
  html, body { width: 1200px; height: 1200px; overflow: hidden; }
  body {
    background: var(--backdrop);
    font-family: "Raleway", sans-serif;
    position: relative;
  }
  .card {
    position: absolute;
    width: 712px;
    height: 418px;
    border-radius: 24px;
    overflow: hidden;
  }
  .card-front { left: 238px; top: 118px; background: var(--plum); }
  .card-back { left: 230px; top: 644px; background: var(--paper); }

  .brand { position: absolute; text-align: center; }
  .brand-square { display: block; margin: 0 auto; }
  .brand-name { font-weight: 400; letter-spacing: -1px; line-height: 1; }

  .card-front .brand { left: 0; right: 0; top: 113px; }
  .card-front .brand-square { width: 102px; height: 100px; background: #fff; }
  .card-front .brand-name { color: #fff; font-size: 64px; margin-top: 18px; }

  .card-back .brand { left: 20px; width: 314px; top: 125px; }
  .card-back .brand-square { width: 76px; height: 74px; background: var(--plum); }
  .card-back .brand-name { color: var(--plum); font-size: 45px; margin-top: 14px; }

  .divider {
    position: absolute; left: 342px; top: 60px; width: 1px; height: 265px;
    background: var(--rule);
  }
  .contact { position: absolute; left: 390px; top: 106px; color: var(--ink); }
  .person-name { color: var(--plum); font-size: 25px; font-weight: 600; }
  .person-title { font-size: 18px; margin-top: 4px; }
  .contact-lines { margin-top: 26px; font-size: 17.5px; line-height: 24px; }
  .contact-row { display: flex; align-items: center; gap: 16px; }
  .contact-row svg { width: 18px; height: 14px; flex: none; }
  .address { margin-top: 4px; font-size: 18px; line-height: 24px; }

  .footer-bands { position: absolute; left: 0; bottom: 0; width: 712px; height: 56px; }
  .website {
    position: absolute; left: 390px; bottom: 16px;
    color: #fff; font-size: 18px;
  }
</style>
</head>
<body>
  <section class="card card-front">
    <div class="brand">
      <span class="brand-square"></span>
      <div class="brand-name">Lanternfold</div>
    </div>
  </section>

  <section class="card card-back">
    <div class="brand">
      <span class="brand-square"></span>
      <div class="brand-name">Lanternfold</div>
    </div>
    <div class="divider"></div>
    <div class="contact">
      <div class="person-name">Nikos Andreou</div>
      <div class="person-title">Your Title</div>
      <div class="contact-lines">
        <div class="contact-row">
          <svg viewBox="0 0 18 14" aria-hidden="true"><path d="M1 5 Q9 -1 17 5 L15 7 L12 5 L12 3 Q9 2 6 3 L6 5 L3 7 Z M4 8 L14 8 L16 13 L2 13 Z" fill="#84205a"/></svg>
          <span>+30 210 555 0148</span>
        </div>
        <div class="contact-row">
          <svg viewBox="0 0 18 14" aria-hidden="true"><rect x="1" y="1" width="16" height="12" fill="#84205a"/><path d="M1 1 L9 8 L17 1 M1 13 L7 6 M17 13 L11 6" stroke="#f7f7f7" stroke-width="1.3" fill="none"/></svg>
          <span>hello@lanternfold-stays.com</span>
        </div>
      </div>
      <div class="address">Your Long Commercial or<br>business address in 2 line</div>
    </div>
    <svg class="footer-bands" viewBox="0 0 712 56" aria-hidden="true">
      <polygon points="0,28 330,28 314,56 0,56" fill="#3f3b3c"/>
      <polygon points="352,0 712,0 712,56 316,56" fill="#84205a"/>
    </svg>
    <div class="website">www.lanternfold-stays.com</div>
  </section>
</body>
</html>
```